Income Tax Flyer - Updates Needed

Just need to update this flyer design and give it a new look. We would like to keep all the same wording but make it stand out a little more. Our selling point is the "Same Day Tax Advance up to $6,000"

Lending, Small Loans, Tax Services, Title Loans, Personal Loans

```html
<!DOCTYPE html>
<html lang="en">
<head>
<meta charset="utf-8">
<title>Same Day Tax Advance Flyer</title>
<link href="https://fonts.googleapis.com/css2?family=Archivo+Black&family=Bebas+Neue&family=Oswald:wght@700&family=Poppins:wght@300;400;500;600;700;800&display=swap" rel="stylesheet">
<style>
  :root {
    --green-deep: #04200f;
    --green-mid: #0e5a31;
    --green-brand: #0d4d2c;
    --red: #c41f27;
    --white: #ffffff;
    --ink: #111111;
    --gold-light: #fff3a0;
    --gold: #e2b928;
    --gold-dark: #b8860b;
  }
  * { margin: 0; padding: 0; box-sizing: border-box; }
  html, body { width: 835px; height: 1200px; overflow: hidden; background: var(--white); }
  .flyer {
    position: relative; width: 835px; height: 1200px; overflow: hidden;
    background: radial-gradient(ellipse at 50% 40%, var(--green-mid) 0%, #0a3d20 45%, var(--green-deep) 100%);
    font-family: "Poppins", sans-serif;
  }
  .money-art {
    position: absolute; inset: 0 0 560px 0;
    background:
      radial-gradient(circle at 6% 8%, rgba(226,185,40,.35), transparent 9%),
      radial-gradient(circle at 95% 6%, rgba(226,185,40,.35), transparent 10%),
      radial-gradient(circle at 8% 48%, rgba(200,210,180,.25), transparent 14%),
      radial-gradient(circle at 90% 32%, rgba(200,210,180,.22), transparent 12%),
      radial-gradient(circle at 86% 60%, rgba(200,210,180,.22), transparent 12%);
  }
  .bottom-sweep { position: absolute; left: 0; top: 0; width: 835px; height: 1200px; }
  .same-day {
    position: absolute; left: 245px; top: 42px; width: 328px; height: 88px;
    background: var(--red); transform: rotate(-2deg);
    display: flex; align-items: center; justify-content: center;
  }
  .same-day span {
    font-family: "Oswald", sans-serif; font-weight: 700; color: var(--white);
    font-size: 60px; letter-spacing: 1px; transform: skewX(-6deg);
  }
  .gold-text {
    background: linear-gradient(180deg, var(--gold-dark) 0%, var(--gold-light) 45%, var(--gold) 70%, var(--gold-dark) 100%);
    -webkit-background-clip: text; background-clip: text; color: transparent;
  }
  .tax {
    position: absolute; left: 186px; top: 96px; width: 440px; text-align: center;
    font-family: "Archivo Black", sans-serif; font-size: 186px; line-height: 1;
    transform: scaleY(1.28) translateY(14px); transform-origin: top center;
    filter: drop-shadow(6px 4px 0 rgba(0,0,0,.55));
  }
  .advance-title {
    position: absolute; left: 404px; top: 290px; display: inline-block; white-space: nowrap;
    font-family: "Bebas Neue", sans-serif; font-size: 198px; line-height: 1;
    transform: translateX(-50%) scaleX(.8); transform-origin: center;
    background: linear-gradient(180deg, #ffffff 0%, #e9e9e9 50%, #a9a9a9 100%);
    -webkit-background-clip: text; background-clip: text; color: transparent;
    filter: drop-shadow(5px 3px 0 rgba(0,0,0,.55));
  }
  .upto {
    position: absolute; left: 262px; top: 454px;
    font-family: "Bebas Neue", sans-serif; font-size: 40px; letter-spacing: 3px;
    color: var(--white); line-height: 1;
  }
  .amount {
    position: absolute; left: 345px; top: 438px; display: inline-block; white-space: nowrap;
    font-family: "Bebas Neue", sans-serif; font-size: 152px; line-height: 1;
    transform: scaleX(.9); transform-origin: left center;
    filter: drop-shadow(4px 3px 0 rgba(0,0,0,.5));
  }
  .lead {
    position: absolute; left: 0; right: 0; top: 720px; text-align: center;
    font-weight: 600; font-size: 28px; color: var(--ink);
  }
  .headline {
    position: absolute; left: 82px; top: 760px; display: flex; align-items: center; gap: 10px;
    font-weight: 800; font-size: 64px; line-height: 1;
  }
  .headline .icon {
    width: 58px; height: 58px; border-radius: 50%; background: var(--ink);
    border: 2px solid var(--white); box-shadow: 0 0 0 2px var(--ink);
    display: flex; align-items: center; justify-content: center;
  }
  .headline .easy { color: var(--red); margin-right: 18px; }
  .headline .advance { color: var(--green-brand); }
  .features { position: absolute; left: 84px; top: 842px; width: 669px; height: 182px; }
  .feature {
    position: absolute; top: 50px; height: 131px; border-radius: 6px; z-index: 2;
    color: var(--white); text-align: center; font-size: 22px; line-height: 1.25;
    display: flex; flex-direction: column; align-items: center; justify-content: center; padding-top: 2px;
  }
  .feature b { font-weight: 700; }
  .feature span { font-weight: 300; }
  .feature--green { background: var(--green-brand); }
  .feature--red { background: var(--red); z-index: 3; }
  .feature-badge {
    position: absolute; top: 0; width: 86px; height: 86px; border-radius: 50%;
    background: var(--white); border: 3px solid var(--green-brand);
    transform: translateX(-50%); z-index: 1;
    display: flex; align-items: flex-start; justify-content: center; padding-top: 5px;
  }
  .feature-badge--red { border-color: var(--red); }
  .feature-badge .ring {
    width: 70px; height: 70px; border-radius: 50%;
    display: flex; align-items: flex-start; justify-content: center; padding-top: 8px;
  }
  .ring--green { background: var(--green-brand); }
  .ring--red { background: var(--red); }
  .brand {
    position: absolute; left: 40px; top: 1072px; width: 228px; text-align: center;
    font-weight: 600; color: var(--green-brand); font-size: 26px; line-height: 1.15;
  }
  .divider { position: absolute; left: 277px; top: 1040px; width: 1px; height: 112px; background: #c9c9c9; }
  .contact-tag {
    position: absolute; left: 293px; top: 1053px; width: 256px; height: 30px;
    background: var(--green-brand); color: var(--white); border-radius: 3px;
    box-shadow: 2px 3px 3px rgba(0,0,0,.3);
    font-weight: 700; font-size: 18.5px; letter-spacing: .4px;
    display: flex; align-items: center; justify-content: center;
  }
  .phone {
    position: absolute; left: 293px; top: 1092px; display: flex; align-items: center; gap: 8px;
    font-weight: 700; font-size: 22px; color: var(--ink);
  }
  .estimates { position: absolute; left: 293px; top: 1120px; font-weight: 800; font-size: 27px; color: var(--ink); }
  .estimates em { font-style: normal; color: var(--red); }
  .location {
    position: absolute; left: 578px; top: 1090px; font-style: normal;
    font-size: 14.5px; line-height: 1.35; color: var(--ink);
  }
  .location .branch { display: flex; align-items: center; gap: 6px; margin-left: -18px; color: var(--red); font-weight: 700; font-size: 15px; }
</style>
</head>
<body>
<main class="flyer">
  <div class="money-art" role="img" aria-label="Falling gold coins and hundred dollar bills scattered around the headline"></div>

  <svg class="bottom-sweep" viewBox="0 0 835 1200" aria-hidden="true">
    <path d="M0 783 C 220 640, 520 560, 835 625 L 835 1200 L 0 1200 Z" fill="var(--red)"/>
    <path d="M0 800 C 230 668, 560 592, 835 688 L 835 1200 L 0 1200 Z" fill="var(--white)"/>
  </svg>

  <div class="same-day"><span>SAME DAY</span></div>
  <div class="tax gold-text">TAX</div>
  <div class="advance-title">ADVANCE</div>
  <div class="upto">UPTO</div>
  <div class="amount gold-text">$6,000</div>

  <p class="lead">File your taxes and apply for an</p>
  <div class="headline">
    <span class="icon">
      <svg width="30" height="30" viewBox="0 0 24 24" aria-hidden="true"><path d="M9 21l-4-5 2-1 2 2V7a1.5 1.5 0 013 0v5l5 1c1 .2 1.6 1 1.5 2l-1 6z" fill="#fff"/><path d="M6 4l2 2M10 2v3M14 4l-2 2" stroke="#fff" stroke-width="1.6" stroke-linecap="round"/></svg>
    </span>
    <span class="easy">EASY</span>
    <span class="icon">
      <svg width="34" height="34" viewBox="0 0 24 24" aria-hidden="true"><circle cx="9" cy="9" r="4.5" fill="none" stroke="#fff" stroke-width="3" stroke-dasharray="2.2 1.3"/><circle cx="9" cy="9" r="1.6" fill="#fff"/><circle cx="16.5" cy="16" r="3.2" fill="none" stroke="#fff" stroke-width="2.4" stroke-dasharray="1.6 1"/></svg>
    </span>
    <span class="advance">ADVANCE!</span>
  </div>

  <section class="features">
    <div class="feature-badge" style="left:113px"><span class="ring ring--green">
      <svg width="36" height="36" viewBox="0 0 24 24" aria-hidden="true"><path d="M4 12a8 8 0 0114-5M20 12a8 8 0 01-14 5" fill="none" stroke="#fff" stroke-width="2.2"/><path d="M18 3v4h-4M6 21v-4h4" fill="none" stroke="#fff" stroke-width="2.2"/><path d="M12 8v4l3 2" fill="none" stroke="#fff" stroke-width="2"/></svg></span></div>
    <div class="feature-badge feature-badge--red" style="left:339px"><span class="ring ring--red">
      <svg width="36" height="36" viewBox="0 0 24 24" aria-hidden="true"><circle cx="13" cy="7" r="5" fill="#fff"/><text x="13" y="10" text-anchor="middle" font-size="8" font-weight="700" fill="#c41f27" font-family="Poppins, sans-serif">$</text><path d="M3 15h3v6H3zM7 16h5l2 1h-4M7 20h7l6-4-2-1-4 2" fill="#fff"/></svg></span></div>
    <div class="feature-badge" style="left:560px"><span class="ring ring--green">
      <svg width="36" height="36" viewBox="0 0 24 24" aria-hidden="true"><circle cx="14" cy="12" r="7" fill="#fff"/><path d="M14 8v4l2.5 2" stroke="#0d4d2c" stroke-width="2" fill="none"/><path d="M2 8h4M1 12h4M2 16h4" stroke="#fff" stroke-width="2" stroke-linecap="round"/></svg></span></div>

    <div class="feature feature--green" style="left:0;width:226px"><span>Available In</span><b>24 Hours or<br>Less</b></div>
    <div class="feature feature--red" style="left:226px;width:226px"><span>Choose Your</span><b>Loan<br>Amount</b></div>
    <div class="feature feature--green" style="left:450px;width:219px;justify-content:flex-start;padding-top:22px"><b>Quick <span>and</span></b><b>Easy</b></div>
  </section>

  <div class="brand">Crestline<br>Financial Group</div>
  <div class="divider"></div>

  <div class="contact-tag">CONTACT US TODAY</div>
  <div class="phone">
    <svg width="20" height="20" viewBox="0 0 24 24" aria-hidden="true"><circle cx="12" cy="12" r="11" fill="var(--green-brand)"/><path d="M8.5 6.5l2 2.5-1.2 1.3c.7 1.6 2 2.9 3.6 3.6l1.3-1.2 2.5 2-1.2 2c-4.5-.3-8.4-4.2-8.7-8.7z" fill="#fff"/></svg>
    555 0142 7788
  </div>
  <div class="estimates"><em>FREE</em> ESTIMATES</div>

  <address class="location">
    <span class="branch"><svg width="12" height="14" viewBox="0 0 24 28" aria-hidden="true"><path d="M12 2a8 8 0 00-8 8c0 6 8 14 8 14s8-8 8-14a8 8 0 00-8-8z" fill="none" stroke="var(--green-brand)" stroke-width="3"/><circle cx="12" cy="10" r="3" fill="var(--green-brand)"/></svg>Riverside – Main Street</span>
    2150-4 N. Main Street<br>Springfield, Texas 78999
  </address>
</main>
</body>
</html>
```